Full re-design of visual identity

We have just re-designed our logo and would like to apply it on our folders, business cards, stationery, and etc... we are attaching new logo + the material we need to re-design... we will provide full corel draw files to help make job easier and also because lot of icons and artwork can be still used...

any doubts we are at your disposal. thanks in advance.

```html
<!DOCTYPE html>
<html lang="en">
<head>
<meta charset="utf-8">
<title>Lumora – Folder and Letterhead</title>
<link href="https://fonts.googleapis.com/css2?family=Open+Sans:wght@400;600;700&family=Dancing+Script:wght@500&display=swap" rel="stylesheet">
<style>
  :root {
    --bg: #ececec;
    --paper: #ffffff;
    --brand-grey: #8c8c8c;
    --text: #3a3a3a;
    --orange: #ee7b2d;
    --orange-light: #f29340;
    --rust: #a8361f;
    --faint: #ededed;
    --bar-grey: #8e8e8e;
  }
  * { margin: 0; padding: 0; box-sizing: border-box; }
  html, body { width: 1200px; height: 1000px; overflow: hidden; }
  body {
    background: var(--bg);
    font-family: "Open Sans", Arial, sans-serif;
    color: var(--text);
    position: relative;
  }
  .sheet {
    position: absolute;
    top: 110px;
    width: 500px;
    height: 720px;
    background: var(--paper);
    box-shadow: 0 8px 24px rgba(0,0,0,0.12);
    overflow: hidden;
  }
  .folder { left: 60px; }
  .letterhead { left: 640px; }

  .brand {
    display: flex;
    align-items: center;
    gap: 8px;
    font-weight: 700;
    color: var(--brand-grey);
    letter-spacing: -0.5px;
  }
  .brand-dot { border-radius: 50%; background: var(--orange); }

  .folder .brand { position: absolute; top: 170px; left: 140px; font-size: 58px; }
  .folder .brand-dot { width: 22px; height: 22px; }

  .folder-band {
    position: absolute;
    left: 0; right: 0;
    top: 470px;
    height: 190px;
    background: linear-gradient(90deg, var(--rust) 0%, var(--orange) 55%, var(--orange-light) 100%);
  }

  .letterhead .brand { position: absolute; top: 40px; right: 40px; font-size: 22px; }
  .letterhead .brand-dot { width: 9px; height: 9px; }

  .letter-decor {
    position: absolute;
    left: 150px; top: 450px;
    width: 310px; height: 160px;
    border-radius: 80px;
    background: var(--faint);
  }

  .letter-body {
    position: absolute;
    top: 110px; left: 50px; right: 50px;
    font-size: 9.5px;
    line-height: 1.45;
  }
  .salutation { margin-bottom: 8px; }
  .letter-body p { margin-bottom: 14px; text-indent: 12px; text-align: justify; }

  .signature {
    position: absolute;
    top: 520px; left: 240px;
    font-family: "Dancing Script", cursive;
    font-size: 30px;
    color: #222;
  }

  .contact {
    position: absolute;
    left: 50px; bottom: 38px;
    font-size: 8px;
    line-height: 1.7;
    display: flex;
    flex-wrap: wrap;
    width: 300px;
    column-gap: 12px;
  }
  .contact span { display: inline-flex; align-items: center; gap: 3px; }
  .contact svg { width: 8px; height: 8px; fill: var(--orange); }

  .footer-bar {
    position: absolute;
    left: 0; right: 0; bottom: 0;
    height: 10px;
    display: flex;
  }
  .footer-bar .grey { flex: 0 0 68%; background: var(--bar-grey); }
  .footer-bar .accent { flex: 1; background: var(--orange); }
  .footer-dot {
    position: absolute;
    right: 40px; bottom: 18px;
    width: 16px; height: 16px;
    border-radius: 50%;
    background: var(--orange);
  }
</style>
</head>
<body>

<section class="sheet folder">
  <div class="brand"><span class="brand-name">Lumora</span><span class="brand-dot"></span></div>
  <div class="folder-band" role="img" aria-label="Large orange brand graphic"></div>
</section>

<section class="sheet letterhead">
  <div class="brand"><span class="brand-name">Lumora</span><span class="brand-dot"></span></div>
  <div class="letter-decor" role="img" aria-label="Faint grey brand graphic"></div>

  <div class="letter-body">
    <div class="salutation">Dear Client,</div>
    <p>Lorem ipsum dolor sit amet, consectetur adipiscing elit. Nulla sodales nisi vitae Lorem ipsum dolor sit amet, consectetur adipiscing elit. Suspendisse feugiat eros nisl, a facilisis risus eleifend sed. Aliquam mauris enim, fermentum eu lacinia sit amet, laoreet eu leo. Nullam eleifend nulla in libero tristique, ac vulputate odio tincidunt. Etiam non condimentum tortor. Integer suscipit neque nec odio porttitor cursus. Phasellus a sapien blandit, suscipit justo id, condimentum ante. Morbi tristique justo risus, id mattis dui molestie ut. Nullam volutpat ut quam commodo faucibus. Pellentesque urna est, interdum in elit quis, pharetra elementum orci. Nam pharetra velit molestie justo placerat scelerisque.</p>
    <p>Ut vitae interdum diam, in euismod ante. Pellentesque volutpat, risus sit amet sodales hendrerit, mi turpis vulputate dolor, eget cursus nulla eros nec tellus. Nulla tincidunt molestie libero vel pretium. Donec condimentum nulla sit amet risus semper imperdiet. Duis congue eros nec diam blandit, et pellentesque sapien auctor. Curabitur iaculis enim lectus, in imperdiet mauris mattis eget. Etiam ac ornare metus. Mauris risus leo, egestas at dolor a, ultrices adipiscing est. Nunc faucibus scelerisque mollis. Pellentesque aliquet mauris tellus, id dignissim risus viverra et. Mauris venenatis lobortis eros. Nam id diam in ligula malesuada feugiat. Cras turpis felis, aliquet id mauris elementum, feugiat ultricies nisl.</p>
  </div>

  <div class="signature">Mark Ellison</div>

  <div class="contact">
    <span><svg viewBox="0 0 10 10"><path d="M2 0h2l1 3-1.5 1a6 6 0 0 0 2.5 2.5L7 5l3 1v2a2 2 0 0 1-2 2A8 8 0 0 1 0 2a2 2 0 0 1 2-2z"/></svg>555-0198-42</span>
    <span><svg viewBox="0 0 10 10"><path d="M5 0a3.5 3.5 0 0 1 3.5 3.5C8.5 6 5 10 5 10S1.5 6 1.5 3.5A3.5 3.5 0 0 1 5 0zm0 2a1.5 1.5 0 1 0 0 3 1.5 1.5 0 0 0 0-3z"/></svg>48, Harbor Lane, Eastfield, Postal Code, Country</span>
    <span><svg viewBox="0 0 10 10"><rect x="0" y="2" width="10" height="6" rx="1"/></svg>555-0198-43</span>
    <span><svg viewBox="0 0 10 10"><path d="M0 2h10v6H0z M0 2l5 3 5-3"/></svg>hello@lumoramail.com</span>
    <span><svg viewBox="0 0 10 10"><circle cx="5" cy="5" r="5"/></svg>www.lumoranet.com</span>
  </div>

  <div class="footer-dot"></div>
  <div class="footer-bar"><span class="grey"></span><span class="accent"></span></div>
</section>

</body>
</html>
```